Lanternfield Drinks business cards

We need a business card design for our new logo. The company is modern, progressive, professional, yet approachable. The key products are ready to drink bottles and cans of coffee based beverages.
These cards will be a critical part of the first impression made by our sales organization, business development team, and all external facing personnel.
Card can be a vertical or horizontal orientation.

Target Market(s)

Customers, suppliers, business partners

Industry/Entity Type

Business

Contact Information for Business Card

Business cards should feature Company Name and Logo.

Font styles to use
Serif

Colors

Designer to choose colors to be used in the design.

Requirements
Must have
• Strong readability of Name, phone #, mobile number and email address.
• Job title, website url, Street Address, and other details can be secondary level readability.
Nice to have
• High impact, simplistic quality design.
• Ok to utilize the 'H in the box' separate from the company name

```html
<!DOCTYPE html>
<html lang="en">
<head>
<meta charset="utf-8">
<title>Lanternfield Drinks — Business Cards</title>
<link rel="stylesheet" href="https://fonts.googleapis.com/css2?family=Crimson+Text:ital,wght@0,400;0,600;1,400&display=swap">
<style>
  :root {
    --backdrop: #b7b7b7;
    --orange-top: #e0852f;
    --orange-bottom: #c04b26;
    --brand-orange: #d2552b;
    --card-white: #f2f2f2;
    --ink: #2a2a2a;
    --divider: #c9a98f;
    --white: #ffffff;
  }
  * { box-sizing: border-box; margin: 0; padding: 0; }
  html, body { width: 1200px; height: 576px; overflow: hidden; }
  body {
    background: var(--backdrop);
    font-family: "Crimson Text", Georgia, serif;
    position: relative;
  }
  .card {
    position: absolute;
    width: 484px;
    height: 292px;
    border-radius: 14px;
    overflow: hidden;
  }
  .card--front {
    left: 82px; top: 139px;
    background: linear-gradient(180deg, var(--orange-top) 0%, var(--orange-bottom) 100%);
  }
  .card--back {
    left: 602px; top: 138px;
    background: var(--card-white);
  }

  /* front */
  .front-mark {
    position: absolute;
    left: 204px; top: 78px;
    width: 76px; height: 76px;
    border: 4px solid var(--white);
  }
  .front-name {
    position: absolute;
    left: 0; right: 0; top: 168px;
    text-align: center;
    color: var(--white);
    font-weight: 600;
    font-size: 34px;
    letter-spacing: 1px;
  }

  /* back */
  .back-mark {
    position: absolute;
    left: 70px; top: 50px;
    width: 69px; height: 69px;
    border: 4px solid var(--brand-orange);
  }
  .back-name {
    position: absolute;
    left: 154px; top: 60px;
    color: var(--brand-orange);
    font-weight: 600;
    font-size: 34px;
    letter-spacing: 0.5px;
    white-space: nowrap;
  }
  .person {
    position: absolute;
    right: 270px; top: 158px;
    text-align: right;
    color: var(--ink);
    line-height: 1;
  }
  .person__name {
    color: var(--brand-orange);
    font-weight: 600;
    font-size: 19px;
    margin-bottom: 4px;
  }
  .person__title {
    font-style: italic;
    font-size: 13px;
    margin-bottom: 8px;
  }
  .person__address {
    font-size: 14px;
    line-height: 18px;
  }
  .divider {
    position: absolute;
    left: 230px; top: 152px;
    width: 1px; height: 83px;
    background: var(--divider);
  }
  .contact {
    position: absolute;
    left: 248px; top: 156px;
    list-style: none;
    color: var(--ink);
    font-size: 14px;
  }
  .contact__item {
    display: flex;
    align-items: center;
    height: 17px;
  }
  .contact__icon {
    width: 12px; height: 12px;
    margin-right: 12px;
    fill: var(--brand-orange);
  }
</style>
</head>
<body>
  <section class="card card--front" aria-label="Card front">
    <div class="front-mark"></div>
    <div class="front-name">Lanternfield Drinks</div>
  </section>

  <section class="card card--back" aria-label="Card back">
    <div class="back-mark"></div>
    <div class="back-name">Lanternfield Drinks</div>

    <div class="person">
      <div class="person__name">John Doe Smith</div>
      <div class="person__title">Managing Director</div>
      <div class="person__address">234 Anywhere St.,<br>Any Town, US 123456</div>
    </div>

    <div class="divider"></div>

    <ul class="contact">
      <li class="contact__item">
        <svg class="contact__icon" viewBox="0 0 12 12"><path d="M1 3.5 Q6 0.5 11 3.5 L10 5 L8 4.5 L8 3.6 Q6 3 4 3.6 L4 4.5 L2 5 Z M2.5 6 H9.5 L10.5 11 H1.5 Z"/></svg>
        555.555.5555
      </li>
      <li class="contact__item">
        <svg class="contact__icon" viewBox="0 0 12 12"><path d="M3 0.5 H9 V11.5 H3 Z M4 1.8 V9 H8 V1.8 Z" fill-rule="evenodd"/></svg>
        666.666.7777
      </li>
      <li class="contact__item">
        <svg class="contact__icon" viewBox="0 0 12 12"><path d="M0.5 2.5 H11.5 V9.5 H0.5 Z"/><path d="M0.8 2.8 L6 6.8 L11.2 2.8" stroke="#f2f2f2" stroke-width="1" fill="none"/></svg>
        johndoe@yourwebsite.com
      </li>
      <li class="contact__item">
        <svg class="contact__icon" viewBox="0 0 12 12"><circle cx="6" cy="6" r="5.5"/><path d="M0.5 6 H11.5 M6 0.5 V11.5 M6 0.5 Q2.5 6 6 11.5 M6 0.5 Q9.5 6 6 11.5" stroke="#f2f2f2" stroke-width="0.8" fill="none"/></svg>
        www.yourwebsite.com
      </li>
    </ul>
  </section>
</body>
</html>
```